Captivating packaging design for sports company.

We need a packaging design that encompasses our resistance bands workout set. Our focus is quality, convenience, and versatility. The design should be tailored to our broad array of customer across all paths. We would like the packaging to reflect our brand and product features such as: the LBS(weight) listed on each of the bands, convenience for travel and at home, highest quality, for all fitness levels, and free eBook. We'd also like to include a couple of our reviews on the packaging. Please refer to our listing on Varlo for additional information https://www.shopvarlo.com/Brisklane-Athletics-Resistance-Workout-Carrying/dp/K47TR2XMNQ/ref=sr_1_1?ie=UTF8&qid=1470453588&sr=8-1&keywords=brisklane+athletics+resistance+bands
Please reach out with additional questions for any further details. Thank you.
Target Market(s)
Sports, fitness, and health enthusiasts of all ages.
Industry/Entity Type
It Company
Look and feel
Each slider illustrates characteristics of the customer's brand and the style your logo design should communicate.

```html
<!DOCTYPE html>
<html lang="en">
<head>
<meta charset="utf-8">
<title>Brisklane Athletics – Resistance Band Packaging</title>
<link rel="stylesheet" href="https://fonts.googleapis.com/css2?family=Exo+2:wght@700&family=Montserrat:wght@300;400;700&display=swap">
<style>
  :root {
    --bg: #e4e4e4;
    --panel: #ffffff;
    --brand-red: #7a1a1f;
    --deep-red: #6e1216;
    --amber: #d98a1c;
    --yellow: #f2d21a;
    --charcoal: #2e2e30;
    --ink: #3a3a3a;
    --edge: #d0d0d0;
  }
  * { box-sizing: border-box; margin: 0; padding: 0; }
  html, body { width: 1200px; height: 900px; overflow: hidden; }
  body {
    background: var(--bg);
    font-family: "Montserrat", sans-serif;
    color: var(--ink);
    position: relative;
  }
  .panel {
    position: absolute;
    background: var(--panel);
    overflow: hidden;
    box-shadow: 0 0 0 1px var(--edge);
  }
  .panel svg.panel-art { position: absolute; inset: 0; }

  /* Lid – top face */
  .lid { left: 380px; top: 50px; width: 620px; height: 580px; }
  .lid .brand { position: absolute; left: 40px; top: 40px; }
  .lid .product-title {
    position: absolute; right: 42px; top: 26px; width: 170px;
    color: #fff; text-align: right;
  }
  .product-title h1 {
    font-weight: 700; font-size: 22px; line-height: 1.08; letter-spacing: 0.2px;
  }
  .product-title p {
    font-weight: 300; font-size: 15px; line-height: 1.2; margin-top: 8px;
  }

  /* Brand lockup */
  .brand { display: flex; align-items: center; gap: 12px; }
  .brand-dot {
    width: 38px; height: 38px; border-radius: 50%;
    background: var(--brand-red); flex: none;
  }
  .brand-name {
    font-family: "Exo 2", sans-serif; font-weight: 700;
    color: var(--brand-red); text-transform: uppercase;
    font-size: 24px; line-height: 0.95; letter-spacing: 0.5px;
  }

  /* Front side */
  .front { left: 380px; top: 630px; width: 620px; height: 220px; }
  .front .brand { position: absolute; left: 190px; top: 72px; gap: 16px; }
  .front .brand-dot { width: 60px; height: 60px; }
  .front .brand-name { font-size: 36px; }

  /* Left side */
  .side { left: 160px; top: 50px; width: 220px; height: 580px; }
  .side .side-title {
    position: absolute; left: 22px; top: 26px;
    writing-mode: vertical-rl; transform: rotate(180deg);
    font-weight: 700; font-size: 18px; color: var(--yellow);
  }
  .side .side-note {
    position: absolute; left: 30px; top: 330px;
    writing-mode: vertical-rl; transform: rotate(180deg);
    font-weight: 400; font-size: 13px; line-height: 1.5; color: var(--ink);
  }
</style>
</head>
<body>

  <section class="panel side" aria-label="Box side panel">
    <svg class="panel-art" width="220" height="580" viewBox="0 0 220 580">
      <defs>
        <linearGradient id="sideWarm" x1="0" y1="0" x2="0" y2="1">
          <stop offset="0" stop-color="#6e1216"/>
          <stop offset="0.55" stop-color="#d98a1c"/>
          <stop offset="1" stop-color="#f2d21a"/>
        </linearGradient>
        <linearGradient id="sidePhoto" x1="0" y1="0" x2="1" y2="0">
          <stop offset="0" stop-color="#f4f4f4"/>
          <stop offset="0.5" stop-color="#c9a890"/>
          <stop offset="1" stop-color="#f4f4f4"/>
        </linearGradient>
      </defs>
      <polygon points="0,0 220,0 220,120 0,300" fill="url(#sideWarm)"/>
      <rect x="90" y="340" width="110" height="200" fill="url(#sidePhoto)" role="img" aria-label="Photo of an athlete stretching a resistance band"/>
      <line x1="70" y1="420" x2="220" y2="455" stroke="#8a2a2a" stroke-width="2"/>
    </svg>
    <div class="side-title">Resistance Band</div>
    <div class="side-note">Train anywhere,<br>every fitness level</div>
  </section>

  <section class="panel lid" aria-label="Box lid">
    <svg class="panel-art" width="620" height="580" viewBox="0 0 620 580">
      <defs>
        <linearGradient id="lidWarm" x1="0" y1="0" x2="0.3" y2="1">
          <stop offset="0" stop-color="#6e1216"/>
          <stop offset="0.5" stop-color="#d98a1c"/>
          <stop offset="1" stop-color="#f2d21a"/>
        </linearGradient>
        <linearGradient id="lidPhoto" x1="0" y1="0" x2="0" y2="1">
          <stop offset="0" stop-color="#6b6b6b"/>
          <stop offset="0.7" stop-color="#9a9a9a"/>
          <stop offset="1" stop-color="#f4f4f4"/>
        </linearGradient>
      </defs>
      <polygon points="360,0 620,0 620,580 520,580" fill="url(#lidWarm)"/>
      <polygon points="350,0 590,0 590,330" fill="#2e2e30"/>
      <rect x="90" y="160" width="340" height="320" fill="url(#lidPhoto)" role="img" aria-label="Photo of an athlete lunging with a resistance band"/>
    </svg>
    <div class="brand">
      <span class="brand-dot"></span>
      <span class="brand-name">Brisklane<br>Athletics</span>
    </div>
    <div class="product-title">
      <h1>Resistance<br>Band</h1>
      <p>Workout Set<br>with<br>Door<br>Anchor</p>
    </div>
  </section>

  <section class="panel front" aria-label="Box front panel">
    <div class="brand">
      <span class="brand-dot"></span>
      <span class="brand-name">Brisklane<br>Athletics</span>
    </div>
  </section>

</body>
</html>
```